Healthcare Service Provider looking for PowerPoint Template

BMV Profile of the company & business activity
===================================
BMV is the leading after-sale healthcare services provider in Kuwait. The IT department in the company sells & executes Healthcare IT projects in hospitals that mainly cover:

1. IT Infrastructure covering data center, disaster recovery, servers, virtualization, backup, redundancy & high-availability, multi-site connectivity, wired & wireless networking, OS & network management, software subscriptions, …etc.

2. Healthcare IT systems covering the Hospital Management system, Electronic Medical Record, evidence-based clinical content, clinical decision support systems, Radiology information system, Lab information system, pharmacy management system, ICU system, dental system, dietary & nutrition system, integration with 3rd party systems in the hospital

3. Human resources covering the company specialized teams of clinical informatics specialists, pharmacists, nurses, project managers, user experience specialists, integration specialists, systems analysts, systems developers, DB administrators, Network administrators, system architects, systems engineers, …

The assortment of these professionals handle the services for implementing specialty Healthcare IT systems, training hospital staff & healthcare professionals, on-site support & maintenance of implemented healthcare systems at the hospital

Requested design job
================
We require a PowerPoint template to be used by the IT department in presenting sales & marketing pitches, commercial proposals, projects, and related to the business activities described in the profile.

The design of the PowerPoint template should:

. be personalized for the business activities of the IT department. promote the corporate brand identity of the company. provide clean, modern and fluent look & feel for presenting on screen, projector or printing. include font selection & design as part of the template design. light colored background

. multiple page layouts & slide types like a cover slide, title slide, different types of content slides, ….

. include design collaterals like icons and clip-arts

. have common design elements in PowerPoint Master slides

Included are the current corporate logos of the company.

In summary, simplicity, fluency and personality are key to the design we seek.

Requirements
Must have
• The design of the PowerPoint template should:
• . be personalized for the business activities of the IT department. promote the corporate brand identity of the company. provide clean, modern and fluent look & feel for presenting on screen, projector or printing. include font selection & design as part of the template design. light colored background
• . multiple page layouts & slide types like a cover slide, title slide, different types of content slides, ….
• . include design collaterals like icons and clip-arts
• . have common design elements in PowerPoint Master slides

```html
<!DOCTYPE html>
<html lang="en">
<head>
<meta charset="utf-8">
<title>BMV Presentation Template</title>
<link href="https://fonts.googleapis.com/css2?family=Ubuntu:wght@300;400;500;700&family=Ubuntu+Condensed&display=swap" rel="stylesheet">
<style>
  :root {
    --page: #e9ebee;
    --navy: #1c2d45;
    --steel: #3d5a73;
    --steel-dark: #2b435a;
    --ink-soft: #8a939c;
    --text: #9aa1a8;
    --rule: #c9ced3;
    --footer: #f2f3f4;
    --white: #ffffff;
  }
  * { box-sizing: border-box; margin: 0; padding: 0; }
  html, body { width: 1200px; height: 1200px; overflow: hidden; }
  body { background: var(--page); font-family: "Ubuntu", sans-serif; color: var(--navy); position: relative; }

  .slide { position: absolute; width: 418px; height: 235px; background: var(--white); overflow: hidden; box-shadow: 0 10px 22px rgba(30,45,70,.08); }
  .col-left { left: 166px; } .col-right { left: 616px; }
  .row-1 { top: 42px; } .row-2 { top: 335px; } .row-3 { top: 629px; } .row-4 { top: 923px; }

  .photo { position: absolute; }
  .title { position: absolute; line-height: 1.05; }
  .title .light { display: block; font-weight: 300; }
  .title .bold { display: block; font-weight: 700; }
  .title-bar { position: absolute; width: 3px; background: var(--navy); }
  .vrule { position: absolute; width: 1px; background: var(--rule); }
  .date { font-size: 7px; font-weight: 300; margin-top: 3px; display: block; }
  .body-text { position: absolute; font-size: 4.6px; line-height: 9.8px; color: var(--text); }
  .body-text p + p { margin-top: 5px; }

  .brand { font-family: "Ubuntu", sans-serif; font-weight: 700; color: var(--navy); letter-spacing: .5px; }
  .partner { display: flex; align-items: center; gap: 4px; font-family: "Ubuntu Condensed", sans-serif; color: var(--navy); }
  .partner .dot { border-radius: 50%; border: 2px solid var(--navy); }

  .footer { position: absolute; left: 0; right: 0; bottom: 0; height: 17px; background: var(--footer); display: flex; align-items: center; padding: 0 22px; gap: 22px; }
  .footer .brand { font-size: 7px; }
  .footer .partner { font-size: 6px; gap: 3px; }
  .footer .partner .dot { width: 8px; height: 8px; border-width: 1.5px; }
  .page-pill { margin-left: auto; background: #c8ccd0; color: var(--white); font-size: 4.5px; border-radius: 4px; padding: 1px 5px; }

  .disc { position: absolute; border-radius: 50%; background: #fafafa; box-shadow: 0 6px 24px rgba(0,0,0,.06); display: flex; flex-direction: column; align-items: center; justify-content: center; text-align: center; }
  .play { position: absolute; width: 44px; height: 44px; border-radius: 50%; background: var(--white); display: flex; align-items: center; justify-content: center; }

  .logo-strip { position: absolute; left: 26px; top: 122px; width: 376px; height: 76px; border: 1px solid #dfe2e5; background: #f6f7f8; display: flex; align-items: center; }
  .logo-strip .cell { flex: 1; height: 44px; display: flex; align-items: center; justify-content: center; }
  .logo-strip .cell + .cell { border-left: 1px solid #d6dadd; }
  .logo-strip .mark { width: 22px; height: 22px; border-radius: 50%; }
</style>
</head>
<body>

<!-- Cover: diagonal -->
<section class="slide col-left row-1">
  <svg class="photo" width="418" height="235" viewBox="0 0 418 235" role="img" aria-label="Photo of a stethoscope, notebook and laptop on a desk">
    <defs>
      <linearGradient id="deskTone" x1="0" y1="0" x2="1" y2="1">
        <stop offset="0" stop-color="#4a6780"/><stop offset="1" stop-color="#2f4a62"/>
      </linearGradient>
    </defs>
    <polygon points="0,0 72,0 0,72" fill="#2f4a62"/>
    <polygon points="258,0 418,0 418,235 58,235" fill="url(#deskTone)"/>
  </svg>
  <div class="brand" style="position:absolute;left:64px;top:60px;font-size:18px;">BMV</div>
  <div style="position:absolute;left:40px;top:84px;font-size:5px;color:var(--navy);">Bright Medical Ventures</div>
  <div class="partner" style="position:absolute;left:55px;top:118px;flex-direction:column;gap:4px;font-size:8px;">
    <span class="dot" style="width:30px;height:30px;border-width:3px;"></span>PARTNER LOGO
  </div>
  <div class="vrule" style="left:187px;top:162px;height:32px;width:2px;background:var(--white);"></div>
  <div class="title" style="left:195px;top:163px;color:var(--white);font-size:13px;">
    <span class="light">Place for the</span><span class="bold">Presentation Title</span>
    <span class="date">22.01.2018</span>
  </div>
</section>

<!-- Cover: light -->
<section class="slide col-right row-1">
  <div class="photo" role="img" aria-label="Faded photo of a bright dental clinic room" style="inset:0;background:linear-gradient(100deg,#fbfbfc 0%,#f4f5f7 45%,#eceef1 100%);"></div>
  <div class="vrule" style="left:24px;top:0;height:206px;"></div>
  <div class="brand" style="position:absolute;left:60px;top:86px;font-size:18px;">BMV</div>
  <div style="position:absolute;left:33px;top:112px;font-size:5px;color:var(--navy);">Bright Medical Ventures</div>
  <div class="vrule" style="left:138px;top:68px;height:122px;"></div>
  <div class="partner" style="position:absolute;left:158px;top:80px;flex-direction:column;gap:6px;font-size:8px;">
    <span class="dot" style="width:30px;height:30px;border-width:3px;"></span>PARTNER LOGO
  </div>
  <div class="title-bar" style="left:22px;top:162px;height:30px;"></div>
  <div class="title" style="left:33px;top:164px;font-size:11.5px;">
    <span class="light">Place for the</span><span class="bold">Presentation Title</span>
    <span class="date" style="color:var(--rule);">22.01.2018</span>
  </div>
</section>

<!-- Title slide with partner -->
<section class="slide col-left row-2">
  <div class="partner" style="position:absolute;left:70px;top:66px;flex-direction:column;gap:8px;font-size:15px;">
    <span class="dot" style="width:64px;height:64px;border-width:6px;"></span>PARTNER LOGO
  </div>
  <div class="vrule" style="left:196px;top:0;height:186px;"></div>
  <div class="title-bar" style="left:195px;top:70px;height:28px;"></div>
  <div class="title" style="left:209px;top:72px;font-size:11px;">
    <span class="light">Place for the</span><span class="bold">Slide Title</span>
  </div>
  <div class="body-text" style="left:209px;top:104px;width:180px;">
    <p>Our teams plan, build and support clinical systems that help hospitals run smoothly. From records to radiology, every project is delivered with care, clear milestones and trained staff on site. We stay close after launch to keep each system fast, safe and ready for patients.</p>
  </div>
  <footer class="footer"><span class="brand">BMV</span><span class="partner"><span class="dot"></span>PARTNER LOGO</span><span class="page-pill">01</span></footer>
</section>

<!-- Text slide -->
<section class="slide col-right row-2">
  <div class="vrule" style="left:24px;top:0;height:40px;"></div>
  <div class="title-bar" style="left:22px;top:28px;height:24px;"></div>
  <div class="title" style="left:33px;top:27px;font-size:11px;">
    <span class="light" style="color:var(--ink-soft);">Place for the</span><span class="bold">Slide Title</span>
  </div>
  <div class="body-text" style="left:33px;top:59px;width:364px;">
    <p>Our teams plan, build and support clinical systems that help hospitals run smoothly. From records to radiology, every project is delivered with care, clear milestones and trained staff on site. We stay close after launch to keep each system fast, safe and ready for patients.</p>
    <p>Data centers, backup, networks and servers form the base of every digital hospital. We design each layer for high availability so clinicians can reach the right record at the right moment, on any ward, on any shift, across every connected site.</p>
    <p>Training and on-site support complete each project. Specialists guide nurses, pharmacists and doctors through daily workflows until the new tools feel familiar and reliable.</p>
  </div>
  <footer class="footer"><span class="brand">BMV</span><span class="partner"><span class="dot"></span>PARTNER LOGO</span><span class="page-pill">01</span></footer>
</section>

<!-- Section break -->
<section class="slide col-left row-3">
  <div class="photo" role="img" aria-label="Soft photo of a dental chair and clinic cabinets" style="inset:0;background:linear-gradient(110deg,#f8f8f9 0%,#eef0f2 50%,#e2e5e8 100%);"></div>
  <div class="disc" style="left:152px;top:53px;width:142px;height:142px;">
    <div class="title" style="position:static;font-size:12px;">
      <span class="light">Section</span><span class="bold">Break</span>
    </div>
  </div>
  <div class="brand" style="position:absolute;left:40px;top:178px;font-size:16px;">BMV</div>
  <div style="position:absolute;left:19px;top:200px;font-size:5px;color:var(--navy);">Bright Medical Ventures</div>
</section>

<!-- Thank you -->
<section class="slide col-right row-3">
  <div class="photo" role="img" aria-label="Photo of a laptop, phone and glasses on a light desk" style="inset:0;background:linear-gradient(110deg,#f4f5f6 0%,#d9dee2 55%,#b7c1c8 100%);"></div>
  <div class="disc" style="left:40px;top:30px;width:180px;height:180px;">
    <span class="brand" style="font-size:15px;">BMV</span>
    <span style="font-size:5px;color:var(--navy);margin-top:3px;">Bright Medical Ventures</span>
    <span style="font-size:12px;font-weight:700;margin-top:22px;">Thank You!</span>
    <span style="font-size:4.8px;font-weight:700;letter-spacing:1.3px;margin-top:2px;">FOR YOUR TIME</span>
  </div>
</section>

<!-- Video grid -->
<section class="slide col-left row-4">
  <div class="photo" role="img" aria-label="Photo of a clipboard, stethoscope and phone on a dark desk" style="left:0;top:0;width:209px;height:109px;background:linear-gradient(135deg,#56677a,#3b4a5a);"></div>
  <div class="play" style="left:73px;top:32px;"><svg width="10" height="10" viewBox="0 0 10 10"><polygon points="2,1 9,5 2,9" fill="var(--navy)"/></svg></div>
  <div class="body-text" style="left:226px;top:10px;width:176px;">
    <p>Our teams plan, build and support clinical systems that help hospitals run smoothly. From records to radiology, every project is delivered with care, clear milestones and trained staff on site. We stay close after launch to keep each system fast, safe and ready for patients.</p>
  </div>
  <div class="vrule" style="left:31px;top:109px;height:81px;"></div>
  <div class="title-bar" style="left:30px;top:149px;height:24px;"></div>
  <div class="title" style="left:43px;top:148px;font-size:11px;">
    <span class="light" style="color:var(--ink-soft);">Place for the</span><span class="bold">Slide Title</span>
  </div>
  <div class="photo" role="img" aria-label="Photo of hands writing a report beside a laptop" style="left:209px;top:109px;width:209px;height:109px;background:linear-gradient(135deg,#6e7c89,#3f4d5b);"></div>
  <div class="play" style="left:280px;top:141px;"><svg width="10" height="10" viewBox="0 0 10 10"><polygon points="2,1 9,5 2,9" fill="var(--navy)"/></svg></div>
  <footer class="footer"><span class="brand">BMV</span><span class="partner"><span class="dot"></span>PARTNER LOGO</span><span class="page-pill">01</span></footer>
</section>

<!-- Logo showcase -->
<section class="slide col-right row-4">
  <div class="vrule" style="left:28px;top:0;height:117px;"></div>
  <div class="title-bar" style="left:27px;top:63px;height:24px;"></div>
  <div class="title" style="left:40px;top:62px;font-size:11px;">
    <span class="light" style="color:var(--ink-soft);">Place for the</span><span class="bold">Slide Title</span>
  </div>
  <div class="body-text" style="left:146px;top:40px;width:256px;">
    <p>Our teams plan, build and support clinical systems that help hospitals run smoothly. From records to radiology, every project is delivered with care, clear milestones and trained staff on site. We stay close after launch to keep each system fast, safe and ready for patients.</p>
  </div>
  <div class="logo-strip">
    <div class="cell"><span class="mark" style="background:#3bb2a0;"></span></div>
    <div class="cell"><span class="mark" style="background:#e64d8c;"></span></div>
    <div class="cell"><span class="mark" style="background:#3fbcb8;"></span></div>
    <div class="cell"><span class="mark" style="background:#f07a3a;"></span></div>
    <div class="cell"><span class="mark" style="background:#3a3f8f;"></span></div>
    <div class="cell"><span class="mark" style="background:#2aa7d8;"></span></div>
  </div>
  <footer class="footer"><span class="brand">BMV</span><span class="partner"><span class="dot"></span>PARTNER LOGO</span><span class="page-pill">01</span></footer>
</section>

</body>
</html>
```